Real estate agent website

I am a new real estate agent and in of a simple but powerful website that is linked to the local Multiple listing services (MLS). It should have a lending page that is connected to my customer relationship management (CRM) software. It must have an ability for potential customers to search for properties and be able to communicate with me easily.
Updates

Updates: The website themes must includes MLS-IDX integration with a grid layout and property slider so i can showcase featured properties. I also would like to have future where potential client can search and have alerts depending on a search criteria.

Industry/Entity Type

Real Estate

Coding

Coded - Design and coding required

Number of Pages Required

3 page

Requirements
Must have
• Home page, Resources page, About Me with contact me window page

```html
<!DOCTYPE html>
<html lang="en">
<head>
<meta charset="utf-8">
<title>Marina Hale – Real Estate Agent</title>
<link rel="stylesheet" href="https://fonts.googleapis.com/css2?family=Montserrat:wght@400;600;700;800&family=Roboto:wght@300;400;500;700&display=swap">
<style>
:root{
  --header:#3f4450;
  --gold:#c9973d;
  --gold-dark:#b8862f;
  --teal:#2e7d77;
  --text:#333;
  --muted:#777;
  --light-bg:#f2f2f2;
  --footer:#262626;
  --amber:#e6a21a;
  --white:#fff;
}
*{box-sizing:border-box;margin:0;padding:0}
html,body{width:1200px;height:3973px;overflow:hidden}
body{font-family:'Roboto',sans-serif;color:var(--text);background:var(--white)}
a{color:inherit;text-decoration:none}

/* Header */
.topbar{height:86px;background:var(--header);display:flex;align-items:center;padding:0 110px;position:relative}
.brand{display:flex;flex-direction:column;align-items:center;color:var(--gold)}
.brand-name{font-family:'Montserrat',sans-serif;font-weight:400;font-size:27px;letter-spacing:3px;line-height:1}
.brand-tag{font-family:'Montserrat',sans-serif;font-weight:400;font-size:10px;letter-spacing:4px;margin-top:6px;color:#d9c9a5}
.contact-item{position:absolute;top:18px;display:flex;align-items:center;gap:12px;color:var(--white)}
.contact-item.phone{left:510px}
.contact-item.mail{left:705px}
.contact-icon{width:36px;height:36px;border-radius:50%;background:var(--gold);display:flex;align-items:center;justify-content:center}
.contact-label{font-size:14px;font-weight:500;line-height:1.2}
.contact-value{font-size:17px;font-weight:700;margin-top:3px}
.contact-item.mail .contact-value{font-size:15px}
.login-btn{position:absolute;right:112px;top:20px;width:120px;height:42px;background:var(--teal);color:var(--white);font-size:15px;font-weight:700;display:flex;align-items:center;justify-content:center;gap:8px}

.mainnav{height:45px;background:var(--gold);display:flex;align-items:center;padding:0 110px;gap:23px;color:var(--white);font-size:15px;font-weight:400;text-transform:uppercase}

/* Hero */
.hero{height:643px;position:relative;background:linear-gradient(160deg,#8d949c 0%,#c9c6c0 35%,#e9e6e0 60%,#4c4e52 100%)}
.hero-photo{position:absolute;inset:0}
.hero-box{position:absolute;left:264px;top:222px;width:670px;height:336px;background:rgba(40,40,40,.6);text-align:center;color:var(--white);padding-top:44px}
.hero-name{font-family:'Montserrat',sans-serif;font-weight:700;font-size:32px}
.hero-title{font-family:'Montserrat',sans-serif;font-weight:800;font-size:42px;margin-top:18px}
.hero-sub{font-family:'Montserrat',sans-serif;font-weight:700;font-size:22px;margin-top:16px}
.hero-search{margin:24px auto 0;width:458px;height:54px;background:var(--white);color:#888;font-size:15px;display:flex;align-items:center;justify-content:center;gap:8px}

/* About */
.about{height:618px;background:var(--light-bg);position:relative}
.about-photo{position:absolute;left:104px;top:103px;width:414px;height:414px;border-radius:50%;background:radial-gradient(circle at 30% 40%,#e4eaf2,#9aa4b0 60%,#5d5048)}
.about-portrait{position:absolute;left:402px;top:350px;width:170px;height:170px;border-radius:50%;border:4px solid var(--white);background:radial-gradient(circle at 50% 45%,#e9c9a8,#c69a6c 60%,#d8d8d8)}
.about-text{position:absolute;left:647px;top:100px;width:442px}
.about-rule{width:58px;height:3px;background:var(--gold);margin-bottom:22px}
.about-heading{font-family:'Montserrat',sans-serif;font-size:32px;font-weight:400;color:#222}
.about-heading strong{font-weight:800}
.about-text p{font-size:15px;line-height:26px;color:#777;font-weight:300;margin-top:12px}
.about-text p + p{margin-top:6px}
.about-actions{display:flex;align-items:center;gap:36px;margin-top:32px}
.btn-gold{width:166px;height:48px;background:var(--gold);color:var(--white);font-weight:700;font-size:15px;display:flex;align-items:center;justify-content:center;gap:8px}
.about-phone{display:flex;align-items:center;gap:14px;font-size:18px;color:#333}

/* Listings */
.listings{height:2082px;position:relative}
.tabs{position:absolute;top:88px;left:396px;display:flex;gap:15px}
.tab{width:201px;height:50px;font-size:15px;font-weight:700;display:flex;align-items:center;justify-content:center;border:1px solid #ddd;background:var(--white);color:#222;box-shadow:0 1px 4px rgba(0,0,0,.12)}
.tab.active{background:var(--teal);color:var(--white);border-color:var(--teal)}
.grid{position:absolute;left:117px;top:204px;width:974px;display:grid;grid-template-columns:repeat(3,304px);column-gap:31px;row-gap:43px}
.card{height:529px;background:var(--white);box-shadow:0 0 10px rgba(0,0,0,.14);padding:6px}
.card-photo{height:213px}
.card-title{text-align:center;font-size:15px;font-weight:700;color:#222;margin-top:22px}
.card-city{text-align:center;font-size:13px;color:#888;margin-top:7px;padding-bottom:14px;border-bottom:1px solid #e5e5e5;margin-left:10px;margin-right:10px}
.features{display:grid;grid-template-columns:1fr 1fr;padding:18px 28px 0 34px;row-gap:20px;font-size:15px;color:#777;border-bottom:1px solid #e5e5e5;margin:0 10px;padding-bottom:20px}
.feat{display:flex;align-items:center;gap:9px}
.price{font-weight:700;color:#222}
.card-meta{display:flex;justify-content:space-between;align-items:center;padding:22px 16px 0 20px}
.badge{width:100px;height:18px;background:#222;border-radius:2px}
.listed{font-size:13px;color:var(--gold)}
.card-foot{position:relative;padding:20px 16px 0 16px;font-size:13px;color:#777;line-height:28px}
.pin{position:absolute;right:18px;bottom:0;width:30px;height:30px;border-radius:50%;background:var(--gold);display:flex;align-items:center;justify-content:center}
.see-more{position:absolute;left:505px;top:1932px;width:200px;height:50px;background:var(--teal);color:var(--white);font-weight:700;font-size:15px;display:flex;align-items:center;justify-content:center}

/* Footer */
.footer{height:499px;background:var(--footer);position:relative;color:var(--white)}
.footer h3{font-size:17px;font-weight:700;text-transform:uppercase;position:absolute;top:82px}
.form{position:absolute;left:108px;top:118px;width:447px;display:grid;grid-template-columns:1fr 1fr;gap:10px}
.field{height:38px;background:var(--white);color:#666;font-size:11px;padding:13px 18px}
.field.message{grid-column:1/3;height:76px}
.submit{position:absolute;left:108px;top:311px;width:146px;height:43px;background:var(--amber);color:var(--white);font-weight:700;font-size:15px;display:flex;align-items:center;justify-content:center}
.quick{position:absolute;left:614px;top:120px;list-style:none;font-size:14px}
.quick li{height:30px;display:flex;align-items:center;gap:14px}
.quick li::before{content:'»';font-size:15px}
.quick li.more a{text-decoration:underline}
.contact-list{position:absolute;left:850px;top:124px;font-size:14px;line-height:24px}
.contact-list div{display:flex;gap:16px;margin-bottom:14px}
.footer-rule{position:absolute;left:108px;right:108px;top:423px;height:1px;background:#444}
.copyright{position:absolute;left:108px;top:444px;font-size:14px}
.social{position:absolute;left:940px;top:437px;display:flex;gap:8px}
.social span{width:32px;height:32px;border-radius:50%;background:var(--white);display:block}
.a11y{position:absolute;left:1125px;top:372px;width:44px;height:44px;border-radius:50%;border:2px solid var(--white);background:#111}
</style>
</head>
<body>

<header>
  <div class="topbar">
    <div class="brand">
      <span class="brand-name">MARINA HALE</span>
      <span class="brand-tag">REAL ESTATE AGENT</span>
    </div>
    <div class="contact-item phone">
      <span class="contact-icon"><svg width="18" height="18" viewBox="0 0 24 24"><path fill="#fff" d="M6.6 10.8a15.2 15.2 0 0 0 6.6 6.6l2.2-2.2c.3-.3.7-.4 1-.2 1.1.4 2.3.6 3.6.6.6 0 1 .4 1 1V20c0 .6-.4 1-1 1A17 17 0 0 1 3 4c0-.6.4-1 1-1h3.5c.6 0 1 .4 1 1 0 1.3.2 2.5.6 3.6.1.3 0 .7-.2 1z"/></svg></span>
      <div><div class="contact-label">Call us</div><div class="contact-value">555-014-2288</div></div>
    </div>
    <div class="contact-item mail">
      <span class="contact-icon"><svg width="18" height="14" viewBox="0 0 20 14"><rect x="1" y="1" width="18" height="12" fill="none" stroke="#fff" stroke-width="2"/><path d="M1 1l9 7 9-7" fill="none" stroke="#fff" stroke-width="2"/></svg></span>
      <div><div class="contact-label">Call us</div><div class="contact-value">mhale.homes@example.com</div></div>
    </div>
    <a class="login-btn" href="#">LOGIN <svg width="11" height="13" viewBox="0 0 11 13"><rect x="0" y="5" width="11" height="8" fill="#fff"/><path d="M2.5 5V3.5a3 3 0 0 1 6 0V5" fill="none" stroke="#fff" stroke-width="1.6"/></svg></a>
  </div>
  <nav class="mainnav">
    <a href="#">Careers With HP</a>
    <a href="#">Search For Properties</a>
    <a href="#">Buyers</a>
    <a href="#">Seller</a>
    <a href="#">Virtual Buy/Sell</a>
    <a href="#">More &#9662;</a>
    <a href="#">Lending</a>
    <a href="#">Contact Us</a>
    <svg width="14" height="14" viewBox="0 0 14 14"><circle cx="6" cy="6" r="4.5" fill="none" stroke="#fff" stroke-width="2"/><path d="M9.5 9.5L13 13" stroke="#fff" stroke-width="2"/></svg>
  </nav>
</header>

<section class="hero">
  <div class="hero-photo" role="img" aria-label="Photo of two people shaking hands over a desk with a small model house, a laptop and a pen"></div>
  <div class="hero-box">
    <div class="hero-name">MARINA HALE</div>
    <div class="hero-title">REAL PEOPLE REAL RESULTS</div>
    <div class="hero-sub">BEGIN YOUR SEARCH BELOW</div>
    <div class="hero-search"><svg width="9" height="13" viewBox="0 0 10 14"><path fill="#888" d="M5 0a5 5 0 0 1 5 5c0 3.5-5 9-5 9S0 8.5 0 5a5 5 0 0 1 5-5zm0 3a2 2 0 1 0 0 4 2 2 0 0 0 0-4z"/></svg>Start Your search by City, Neighborhood or Zipcode</div>
  </div>
</section>

<section class="about">
  <div class="about-photo" role="img" aria-label="Photo of a woman holding house plans in front of a home"></div>
  <div class="about-portrait" role="img" aria-label="Portrait photo of the agent"></div>
  <div class="about-text">
    <div class="about-rule"></div>
    <h2 class="about-heading"><strong>ABOUT</strong> MARINA HALE</h2>
    <p>Purchasing or selling a house is the biggest investment venture that most of us will have in our lifetime. A home is a place of comfort and love. It is where we create memories. A place to live with our families and pets and enjoy our friends, and it's a place where we create life-long memories.</p>
    <p>No matter what your goal or needs are in real estate, I would be honored to guide you through this journey. This is never just a business transaction; it will be a time where we would learn how to build trust that will sail our "ship" of relations throughout the years. One happy client at a time!</p>
    <div class="about-actions">
      <a class="btn-gold" href="#">LEARN MORE <svg width="13" height="13" viewBox="0 0 14 14"><circle cx="7" cy="7" r="7" fill="#fff"/><path d="M5.5 4l3 3-3 3" fill="none" stroke="#c9973d" stroke-width="2"/></svg></a>
      <span class="about-phone"><span class="contact-icon" style="background:var(--teal)"><svg width="18" height="18" viewBox="0 0 24 24"><path fill="#fff" d="M6.6 10.8a15.2 15.2 0 0 0 6.6 6.6l2.2-2.2c.3-.3.7-.4 1-.2 1.1.4 2.3.6 3.6.6.6 0 1 .4 1 1V20c0 .6-.4 1-1 1A17 17 0 0 1 3 4c0-.6.4-1 1-1h3.5c.6 0 1 .4 1 1 0 1.3.2 2.5.6 3.6.1.3 0 .7-.2 1z"/></svg></span>(555) 014-2288</span>
    </div>
  </div>
</section>

<section class="listings">
  <div class="tabs">
    <a class="tab active" href="#">FEATURED LISTINGS</a>
    <a class="tab" href="#">ALL LISTINGS</a>
  </div>

  <div class="grid">
    <article class="card">
      <div class="card-photo" role="img" aria-label="Photo of a red and beige townhome building" style="background:linear-gradient(#cfe0ef 0%,#9d4a42 45%,#c8b99f 75%,#6f8a4c 100%)"></div>
      <h4 class="card-title">1520 Birchwood Ave N 3604 (# 104)</h4>
      <div class="card-city">Maple Grove, MN 55311</div>
      <div class="features"><span class="feat">▭ 2 Bed Rooms</span><span class="feat">◡ 1 Bath</span><span class="feat">⌂ 1,340 Sqft</span><span class="feat price">$295,000</span></div>
      <div class="card-meta"><span class="badge"></span><span class="listed">Listed 1 Day Ago</span></div>
      <div class="card-foot">MLS# NST6300101<br>Listing Office: Northpoint Realty<span class="pin"><svg width="10" height="14" viewBox="0 0 10 14"><path fill="#fff" d="M5 0a5 5 0 0 1 5 5c0 3.5-5 9-5 9S0 8.5 0 5a5 5 0 0 1 5-5zm0 3a2 2 0 1 0 0 4 2 2 0 0 0 0-4z"/></svg></span></div>
    </article>

    <article class="card">
      <div class="card-photo" role="img" aria-label="Photo of row townhomes along a sidewalk" style="background:linear-gradient(#a9c9ea 0%,#d4cbb6 45%,#8f8b7f 70%,#6e9a48 100%)"></div>
      <h4 class="card-title">8420 Aspen Lane N</h4>
      <div class="card-city">Maple Grove, MN 55369</div>
      <div class="features"><span class="feat">▭ 2 Bed Rooms</span><span class="feat">◡ 1 Bath</span><span class="feat">⌂ 1,248</span><span class="feat price">$315,000</span></div>
      <div class="card-meta"><span class="badge"></span><span class="listed">Listed 2 Day Ago</span></div>
      <div class="card-foot">MLS# NST6300102<br>Listing Office: Keystone Home Group<span class="pin"><svg width="10" height="14" viewBox="0 0 10 14"><path fill="#fff" d="M5 0a5 5 0 0 1 5 5c0 3.5-5 9-5 9S0 8.5 0 5a5 5 0 0 1 5-5zm0 3a2 2 0 1 0 0 4 2 2 0 0 0 0-4z"/></svg></span></div>
    </article>

    <article class="card">
      <div class="card-photo" role="img" aria-label="Photo of a single-storey house with garage in snow" style="background:linear-gradient(#6fa4dc 0%,#c8d2dc 40%,#9aa3ad 65%,#f2f4f6 100%)"></div>
      <h4 class="card-title">16540 91st Place N</h4>
      <div class="card-city">Maple Grove, MN 55311</div>
      <div class="features"><span class="feat">▭ 4 Bed Rooms</span><span class="feat">◡ 3Bath</span><span class="feat">⌂ 1,340 Sqft</span><span class="feat price">$295,000</span></div>
      <div class="card-meta"><span class="badge"></span><span class="listed">Listed 2 Day Ago</span></div>
      <div class="card-foot">MLS# NST6300103<br>Listing Office: Prairie Lane RE<span class="pin"><svg width="10" height="14" viewBox="0 0 10 14"><path fill="#fff" d="M5 0a5 5 0 0 1 5 5c0 3.5-5 9-5 9S0 8.5 0 5a5 5 0 0 1 5-5zm0 3a2 2 0 1 0 0 4 2 2 0 0 0 0-4z"/></svg></span></div>
    </article>

    <article class="card">
      <div class="card-photo" role="img" aria-label="Photo of a two-storey house behind bare trees in winter" style="background:linear-gradient(#b8cde2 0%,#8a7a68 40%,#c9b89d 60%,#f0f2f4 100%)"></div>
      <h4 class="card-title">8712 Lilac Lane N</h4>
      <div class="card-city">Maple Grove, MN 55311</div>
      <div class="features"><span class="feat">▭ 4 Bed Rooms</span><span class="feat">◡ 4 Bath</span><span class="feat">⌂ 2,714</span><span class="feat price">$12,196.8</span></div>
      <div class="card-meta"><span class="badge"></span><span class="listed">Listed 4 Day Ago</span></div>
      <div class="card-foot">MLS# NST6300104<br>Listing Office: Oakfield REG<span class="pin"><svg width="10" height="14" viewBox="0 0 10 14"><path fill="#fff" d="M5 0a5 5 0 0 1 5 5c0 3.5-5 9-5 9S0 8.5 0 5a5 5 0 0 1 5-5zm0 3a2 2 0 1 0 0 4 2 2 0 0 0 0-4z"/></svg></span></div>
    </article>

    <article class="card">
      <div class="card-photo" role="img" aria-label="Photo of a grey house among pine trees with snowy driveway" style="background:linear-gradient(#3f6ea8 0%,#3d4a3a 40%,#7c858e 60%,#e9eef3 100%)"></div>
      <h4 class="card-title">13610 Pine Ridge Drive</h4>
      <div class="card-city">Maple Grove, MN 55311</div>
      <div class="features"><span class="feat">▭ 4 Bed Rooms</span><span class="feat">◡ 4 Bath</span><span class="feat">⌂ 2,637</span><span class="feat price">$546,900</span></div>
      <div class="card-meta"><span class="badge"></span><span class="listed">Listed 5 Day Ago</span></div>
      <div class="card-foot">MLS# NST6300105<br>Listing Office: Harbor Realty, Inc.<span class="pin"><svg width="10" height="14" viewBox="0 0 10 14"><path fill="#fff" d="M5 0a5 5 0 0 1 5 5c0 3.5-5 9-5 9S0 8.5 0 5a5 5 0 0 1 5-5zm0 3a2 2 0 1 0 0 4 2 2 0 0 0 0-4z"/></svg></span></div>
    </article>

    <article class="card">
      <div class="card-photo" role="img" aria-label="Photo of a brick two-storey house in snow" style="background:linear-gradient(#9fbbd8 0%,#8a5c44 40%,#b58a6a 60%,#f1f3f5 100%)"></div>
      <h4 class="card-title">8930 Juniper Lane N</h4>
      <div class="card-city">Maple Grove, MN 55311</div>
      <div class="features"><span class="feat">▭ 4 Bed Rooms</span><span class="feat">◡ 3 Bath</span><span class="feat">⌂ 2,587</span><span class="feat price">$565,000</span></div>
      <div class="card-meta"><span class="badge"></span><span class="listed">Listed 6 Day Ago</span></div>
      <div class="card-foot">MLS# NST6300106<br>Listing Office: Prairie Lane RE<span class="pin"><svg width="10" height="14" viewBox="0 0 10 14"><path fill="#fff" d="M5 0a5 5 0 0 1 5 5c0 3.5-5 9-5 9S0 8.5 0 5a5 5 0 0 1 5-5zm0 3a2 2 0 1 0 0 4 2 2 0 0 0 0-4z"/></svg></span></div>
    </article>

    <article class="card">
      <div class="card-photo" role="img" aria-label="Aerial photo of a white house surrounded by green trees" style="background:linear-gradient(#a9c8e6 0%,#4e7a36 35%,#7ea35a 70%,#8f8f86 100%)"></div>
      <h4 class="card-title">8806 Elmstead Court</h4>
      <div class="card-city">Maple Grove, MN 55311</div>
      <div class="features"><span class="feat">▭ 4 Bed Rooms</span><span class="feat">◡ 2 Bath</span><span class="feat">⌂ 2,845</span><span class="feat price">$850,000</span></div>
      <div class="card-meta"><span class="badge"></span><span class="listed">Listed 7 Day Ago</span></div>
      <div class="card-foot">MLS# NST6300107<br>Listing Office: Willowmere Realty, Inc.<span class="pin"><svg width="10" height="14" viewBox="0 0 10 14"><path fill="#fff" d="M5 0a5 5 0 0 1 5 5c0 3.5-5 9-5 9S0 8.5 0 5a5 5 0 0 1 5-5zm0 3a2 2 0 1 0 0 4 2 2 0 0 0 0-4z"/></svg></span></div>
    </article>

    <article class="card">
      <div class="card-photo" role="img" aria-label="Photo of a bright living room with grey sofa and fireplace" style="background:linear-gradient(#eef0f1 0%,#d9dbdc 45%,#7d7f82 70%,#b9a58a 100%)"></div>
      <h4 class="card-title">13610 Pine Ridge Drive</h4>
      <div class="card-city">Maple Grove, MN 55311</div>
      <div class="features"><span class="feat">▭ 3 Bed Rooms</span><span class="feat">◡ 4 Bath</span><span class="feat">⌂ 2,263</span><span class="feat price">$440,000</span></div>
      <div class="card-meta"><span class="badge"></span><span class="listed">Listed 8 Day Ago</span></div>
      <div class="card-foot">MLS# NST6300108<br>Listing Office: Northpoint Realty<span class="pin"><svg width="10" height="14" viewBox="0 0 10 14"><path fill="#fff" d="M5 0a5 5 0 0 1 5 5c0 3.5-5 9-5 9S0 8.5 0 5a5 5 0 0 1 5-5zm0 3a2 2 0 1 0 0 4 2 2 0 0 0 0-4z"/></svg></span></div>
    </article>

    <article class="card">
      <div class="card-photo" role="img" aria-label="Photo of an open kitchen and dining area" style="background:linear-gradient(#f1f1ef 0%,#cfcac2 40%,#6d6863 65%,#8c7f92 100%)"></div>
      <h4 class="card-title">8930 Juniper Lane N</h4>
      <div class="card-city">Maple Grove, MN 55311</div>
      <div class="features"><span class="feat">▭ 5 Bed Rooms</span><span class="feat">◡ 3 Bath</span><span class="feat">⌂ 2,568</span><span class="feat price">$469,900</span></div>
      <div class="card-meta"><span class="badge"></span><span class="listed">Listed 9 Day Ago</span></div>
      <div class="card-foot">MLS# NST6300109<br>Listing Office: Keystone Home Group<span class="pin"><svg width="10" height="14" viewBox="0 0 10 14"><path fill="#fff" d="M5 0a5 5 0 0 1 5 5c0 3.5-5 9-5 9S0 8.5 0 5a5 5 0 0 1 5-5zm0 3a2 2 0 1 0 0 4 2 2 0 0 0 0-4z"/></svg></span></div>
    </article>
  </div>

  <a class="see-more" href="#">SEE MORE &nbsp;LISTINGS</a>
</section>

<footer class="footer">
  <h3 style="left:108px">Get In Touch</h3>
  <div class="form">
    <div class="field">First Name</div>
    <div class="field">Last Name</div>
    <div class="field">Email</div>
    <div class="field">Phone Number</div>
    <div class="field message">Message</div>
  </div>
  <a class="submit" href="#">SUBMIT NOW</a>

  <h3 style="left:614px">Quick Links</h3>
  <ul class="quick">
    <li><a href="#">Careers With Hp</a></li>
    <li><a href="#">Search For Properties</a></li>
    <li><a href="#">Buyers</a></li>
    <li><a href="#">Seller</a></li>
    <li><a href="#">Virtual Buy/sell</a></li>
    <li><a href="#">Wisconsin Agents</a></li>
    <li><a href="#">New Construction</a></li>
    <li><a href="#">Builders</a></li>
    <li class="more"><a href="#">More</a></li>
  </ul>

  <h3 style="left:850px">Contact Us</h3>
  <div class="contact-list">
    <div><svg width="10" height="14" viewBox="0 0 10 14" style="margin-top:5px;flex:none"><path fill="#fff" d="M5 0a5 5 0 0 1 5 5c0 3.5-5 9-5 9S0 8.5 0 5a5 5 0 0 1 5-5zm0 3a2 2 0 1 0 0 4 2 2 0 0 0 0-4z"/></svg><span>820 Lakeview Parkway<br>Suite 140 Cedar Hollow,<br>MN, 55400</span></div>
    <div><svg width="9" height="14" viewBox="0 0 9 14" style="margin-top:5px;flex:none"><rect x="1" y="1" width="7" height="12" rx="1" fill="none" stroke="#fff" stroke-width="1.6"/></svg><span>555-014-2288</span></div>
    <div><svg width="14" height="11" viewBox="0 0 20 14" style="margin-top:7px;flex:none"><rect x="1" y="1" width="18" height="12" fill="none" stroke="#fff" stroke-width="2"/><path d="M1 1l9 7 9-7" fill="none" stroke="#fff" stroke-width="2"/></svg><span>mhale.homes@example.com</span></div>
  </div>

  <div class="a11y" role="img" aria-label="Accessibility options"></div>
  <div class="footer-rule"></div>
  <div class="copyright">© Marina Hale 2023 &nbsp; | &nbsp; All Rights Reserved &nbsp; | &nbsp; Terms and Conditions</div>
  <div class="social" aria-label="Social links"><span></span><span></span><span></span><span></span></div>
</footer>

</body>
</html>
```